Wordpress Design for a Private Label BBQ Brand

For our new brand, we'd need a new Wordpress website. We'd prefer to run the website on Wordpress

We'd like to include the following
- space for description of the brand
- space for product portfolio (not a shop!)
- space for socials
- space for support
- space for contact

```html
<!DOCTYPE html>
<html lang="en">
<head>
<meta charset="utf-8">
<title>Brasero — Smokers and Charcoal Grills</title>
<link href="https://fonts.googleapis.com/css2?family=Libre+Baskerville:wght@400;700&family=Montserrat:wght@400;500;600;700&display=swap" rel="stylesheet">
<style>
:root{
  --orange:#e8601c;
  --red:#c8202a;
  --blue:#3a78c4;
  --blue-dark:#2a55a3;
  --ink:#1c1c1c;
  --night:#141414;
  --white:#ffffff;
  --muted:#6b6b6b;
  --serif:'Libre Baskerville', Georgia, serif;
  --sans:'Montserrat', Arial, sans-serif;
}
*{margin:0;padding:0;box-sizing:border-box}
html,body{width:1200px;height:4149px;overflow:hidden}
body{position:relative;background:var(--white);font-family:var(--sans);color:var(--ink)}
.abs{position:absolute}
.fill{position:absolute}

/* hero */
.hero{position:absolute;left:0;top:0;width:1200px;height:660px;background:linear-gradient(180deg,#3a3a35 0%,#2b2620 40%,#3d2a1c 70%,#1e1a17 100%);overflow:hidden}
.hero-photo{position:absolute;inset:0;background:radial-gradient(ellipse at 35% 70%,rgba(190,110,50,.45),transparent 60%),radial-gradient(ellipse at 70% 15%,rgba(120,130,90,.35),transparent 50%)}
.hero-accent{position:absolute;left:0;top:0}
.logo{position:absolute;left:100px;top:38px;font-family:var(--serif);font-weight:700;font-size:23px;color:var(--white);display:flex;align-items:center;gap:8px}
.logo .dot{width:12px;height:12px;border-radius:50%;background:var(--orange)}
.nav{position:absolute;left:348px;top:40px;display:flex;gap:38px;font-family:var(--serif);font-weight:700;font-size:11px;letter-spacing:.5px;color:var(--white)}
.nav .active{position:relative}
.nav .active:after{content:"";position:absolute;left:8px;right:8px;bottom:-8px;height:2px;background:var(--orange)}
.call{position:absolute;left:856px;top:22px;display:flex;gap:14px;align-items:flex-start}
.call-badge{width:50px;height:55px;background:var(--blue);display:flex;align-items:center;justify-content:center;clip-path:polygon(0 0,100% 0,100% 88%,0 100%)}
.call-label{font-family:var(--serif);font-weight:700;font-size:12px;color:var(--blue);margin-top:6px;letter-spacing:.3px}
.hero h1{position:absolute;left:100px;top:185px;font-family:var(--serif);font-weight:700;font-size:70px;line-height:76px;color:var(--white)}
.hero .rule{position:absolute;left:103px;top:355px;width:80px;height:5px;background:var(--blue)}
.hero .tagline{position:absolute;left:103px;top:388px;font-size:20px;color:var(--white);letter-spacing:.3px}
.btn{position:absolute;display:flex;align-items:center;justify-content:center;font-family:var(--serif);font-weight:700;font-size:12px;color:var(--white);letter-spacing:.3px}
.btn-blue{background:linear-gradient(180deg,#4a8ad6,var(--blue-dark))}
.btn-orange{background:linear-gradient(90deg,var(--orange),var(--red))}

/* welcome */
.welcome h2{position:absolute;left:600px;top:810px;font-family:var(--serif);font-weight:700;font-size:40px;line-height:50px;color:var(--ink)}
.welcome h2 span{color:var(--orange)}
.welcome p{position:absolute;left:600px;top:928px;width:520px;font-size:13.5px;line-height:25px;color:#333}

/* accessories */
.accessories h2{position:absolute;left:103px;top:1495px;font-family:var(--serif);font-weight:700;font-size:40px;line-height:49px;color:var(--white)}
.accessories p{position:absolute;left:103px;top:1605px;width:560px;font-size:13.5px;line-height:20px;color:#e5eefa}

/* section titles */
.section-title{position:absolute;left:0;width:1200px;text-align:center;font-family:var(--serif);font-weight:700;font-size:40px}
.section-title .hl{color:var(--orange)}
.title-rule{position:absolute;left:500px;width:164px;height:4px;background:linear-gradient(90deg,var(--orange),var(--red))}

/* products */
.product{position:absolute;width:300px;text-align:center}
.product .name{font-weight:600;font-size:19px;color:var(--orange)}
.product .desc{font-size:12.5px;margin-top:14px;color:#333}
.arrow{position:absolute;width:52px;height:52px;border-radius:50%;background:var(--white);box-shadow:0 2px 8px rgba(0,0,0,.15);display:flex;align-items:center;justify-content:center}

/* news */
.news{position:absolute;left:0;top:2553px;width:1200px;height:701px;background:radial-gradient(ellipse at 30% 40%,#2a2a2a,var(--night) 70%)}
.card{position:absolute;top:2763px;width:309px;height:338px;background:var(--white);border-radius:6px;overflow:hidden}
.card .img{height:177px}
.card .date{position:absolute;left:12px;top:12px;background:var(--blue);color:var(--white);font-size:12px;font-weight:600;padding:3px 6px;border-radius:3px}
.card h3{margin:20px 0 0 16px;font-weight:600;font-size:21px;color:var(--ink)}
.card p{margin:10px 14px 0 14px;font-size:12.5px;line-height:19px;color:#888}
.dots{position:absolute;top:3151px;left:570px;display:flex;gap:8px}
.dots span{width:14px;height:14px;border-radius:50%;background:var(--white)}
.dots span.on{background:var(--blue)}

/* map + enquiry */
.map{position:absolute;left:0;top:3254px;width:1200px;height:480px;background:linear-gradient(120deg,#efe4cf 0%,#e6dcc4 45%,#c9e0c4 70%,#efe6d2 100%)}
.enquiry{position:absolute;left:100px;top:3399px;width:338px;height:545px}
.enquiry-head{position:absolute;left:0;top:0;width:338px;height:106px;background:#0e0e0e;color:var(--white);font-family:var(--serif);font-weight:700;font-size:28px;padding:44px 0 0 32px}
.enquiry-body{position:absolute;left:0;top:106px;width:338px;height:439px;background:linear-gradient(135deg,var(--orange),var(--red));clip-path:polygon(0 0,100% 0,100% 87%,0 100%)}
.field{position:absolute;left:33px;width:280px;border-bottom:1px solid rgba(255,255,255,.8);color:var(--white);font-size:11px;padding-bottom:12px}
.send{position:absolute;left:36px;top:315px;width:118px;height:40px;background:var(--white);color:var(--ink);font-family:var(--serif);font-weight:700;font-size:12px;display:flex;align-items:center;justify-content:center}

/* footer */
.footer{position:absolute;left:0;top:3734px;width:1200px;height:415px;background:var(--night)}
.footer h4{position:absolute;font-family:var(--serif);font-weight:700;font-size:19px;color:var(--white)}
.links{position:absolute;list-style:none;font-size:12.5px;color:#ddd}
.links li{height:33px}
.footer-brand{position:absolute;left:880px;top:124px;width:240px;text-align:center;font-family:var(--serif);font-weight:700;font-size:24px;color:var(--white)}
.social{position:absolute;top:188px;width:44px;height:44px;border-radius:50%;border:2px solid #444;background:#1f1f1f}
.copyright{position:absolute;left:0;top:352px;width:1200px;text-align:center;font-size:12px;color:#ddd}
.divider{position:absolute;top:313px;height:1px;width:18px;background:var(--red)}
</style>
</head>
<body>

<header class="hero">
  <div class="hero-photo" role="img" aria-label="Blurred photo of food cooking on a charcoal grill at an outdoor gathering"></div>
  <svg class="hero-accent" width="1200" height="660" aria-hidden="true">
    <defs><linearGradient id="heroRed" x1="0" y1="1" x2="1" y2="0"><stop offset="0" stop-color="#e8601c"/><stop offset="1" stop-color="#c8202a"/></linearGradient></defs>
    <polygon points="580,660 1200,160 1200,660" fill="url(#heroRed)"/>
  </svg>
  <div class="logo"><span class="dot"></span>BRASERO</div>
  <nav class="nav"><span class="active">HOME</span><span>ABOUT US</span><span>PRODUCTS</span><span>NEWS</span><span>CONTACT</span></nav>
  <div class="call">
    <div class="call-badge"><svg width="22" height="22" viewBox="0 0 24 24" fill="#fff" aria-hidden="true"><path d="M6.6 10.8a15.1 15.1 0 0 0 6.6 6.6l2.2-2.2a1 1 0 0 1 1-.25 11.4 11.4 0 0 0 3.6.57 1 1 0 0 1 1 1V20a1 1 0 0 1-1 1A17 17 0 0 1 3 4a1 1 0 0 1 1-1h3.5a1 1 0 0 1 1 1c0 1.25.2 2.45.57 3.57a1 1 0 0 1-.25 1z"/></svg></div>
    <div class="call-label">CALL US TODAY!</div>
  </div>
  <h1>Smokkers and<br>Charcoal Grills</h1>
  <div class="rule"></div>
  <div class="tagline">BUILT FOR GENERATIONS</div>
  <div class="btn btn-blue" style="left:105px;top:451px;width:190px;height:49px">CONTACT NOW</div>
</header>
<div class="fill" role="img" aria-label="Black ceramic kamado smoker grill on metal legs" style="left:810px;top:217px;width:250px;height:470px;background:radial-gradient(ellipse at 50% 35%,#3a3a3a,#111 70%);border-radius:48% 48% 10% 10%"></div>

<section class="welcome">
  <div class="fill" role="img" aria-label="Round charcoal grill loaded with meat and skewers beside an open black kamado grill" style="left:105px;top:733px;width:425px;height:467px;background:radial-gradient(circle at 35% 35%,#6b3a22 0%,#2a1a14 45%,transparent 62%),radial-gradient(ellipse at 70% 60%,#2b2b2b 0%,#111 35%,transparent 52%)"></div>
  <h2>WELCOME TO<br><span>BRASERO</span></h2>
  <p>Lorem Ipsum is simply dummy text of the printing and typesetting industry. Lorem Ipsum has been the industry's standard dummy text ever since the 1500s, when an unknown printer took a galley of type and scrambled it to make a type specimen book. It has survived not only five centuries, but also the leap into electronic typesetting</p>
  <div class="btn btn-orange" style="left:600px;top:1120px;width:154px;height:43px">MORE ABOUT</div>
  <div class="btn btn-blue" style="left:786px;top:1120px;width:171px;height:43px">CONTACT NOW</div>
</section>

<section class="accessories">
  <svg class="abs" style="left:0;top:1225px" width="1200" height="716" aria-hidden="true">
    <defs><linearGradient id="accBlue" x1="0" y1="0" x2="1" y2="0"><stop offset="0" stop-color="#4a8fd0"/><stop offset="1" stop-color="#2a55a3"/></linearGradient></defs>
    <polygon points="0,141 1200,0 1200,563 0,716" fill="url(#accBlue)"/>
  </svg>
  <h2>BRASERO<br>ACCESSORIES</h2>
  <p>Lorem Ipsum is simply dummy text of the printing and typesetting industry. Lorem Ipsum has been the industry's standard dummy text ever since the 1500s, when an unknown printer took a galley of type and scrambled it to make a type specimen book. It has survived not only five centuries, but also the leap into electronic typesetting</p>
  <div class="btn btn-orange" style="left:101px;top:1746px;width:226px;height:41px">VIEW OUR ACCESSORIES</div>
  <div class="fill" role="img" aria-label="Grill fork and spatula with wooden handles beside a grill of vegetable skewers" style="left:733px;top:1377px;width:467px;height:451px;background:radial-gradient(ellipse at 85% 50%,#6a4a2a 0%,#2a2a2a 40%,transparent 62%),linear-gradient(110deg,transparent 15%,rgba(160,90,40,.35) 30%,transparent 45%)"></div>
</section>

<section class="products">
  <div class="section-title" style="top:1960px"><span class="hl">BRASERO</span> PRODUCTS</div>
  <div class="title-rule" style="top:2018px"></div>
  <div class="arrow" style="left:67px;top:2226px"><svg width="14" height="14" viewBox="0 0 14 14" aria-hidden="true"><path d="M9 2 4 7l5 5" stroke="#333" stroke-width="2" fill="none"/></svg></div>
  <div class="arrow" style="left:1064px;top:2226px"><svg width="14" height="14" viewBox="0 0 14 14" aria-hidden="true"><path d="m5 2 5 5-5 5" stroke="#333" stroke-width="2" fill="none"/></svg></div>

  <div class="fill" role="img" aria-label="Black kamado grill product" style="left:160px;top:2078px;width:150px;height:250px;background:radial-gradient(ellipse at 50% 35%,#3a3a3a,#111 60%,transparent 72%)"></div>
  <div class="fill" role="img" aria-label="Grill tool set in an aluminium case" style="left:495px;top:2115px;width:185px;height:180px;background:linear-gradient(180deg,#d8d8d8,#8a8a8a);border-radius:6px"></div>
  <div class="fill" role="img" aria-label="Tongs, fork and spatula grill tools" style="left:865px;top:2113px;width:150px;height:170px;background:linear-gradient(90deg,transparent 8%,#555 10%,#555 16%,transparent 18%,transparent 45%,#666 47%,#666 53%,transparent 55%,transparent 80%,#777 82%,#777 92%,transparent 94%)"></div>

  <div class="product" style="left:85px;top:2356px"><div class="name">Product Name</div><div class="desc">Desription goes here</div></div>
  <div class="product" style="left:433px;top:2356px"><div class="name">Product Name</div><div class="desc">Desription goes here</div></div>
  <div class="product" style="left:780px;top:2356px"><div class="name">Product Name</div><div class="desc">Desription goes here</div></div>
</section>

<section class="news" aria-label="News"></section>
<div class="section-title" style="top:2643px;color:var(--white)"><span class="hl">BRASERO</span> NEWS</div>
<article class="card" style="left:93px"><div class="img" role="img" aria-label="Corn and meat cooking on a charcoal kettle grill" style="background:linear-gradient(160deg,#5a4a3a,#a07040 50%,#2a2a2a)"></div><span class="date">July 30,2019</span><h3>Lorem Ipsum is a dummy</h3><p>Lorem Ipsum is simply dummy text of the a printing and typesetting ever since indus-try Lorem Ipsum is simply dummy text of</p></article>
<article class="card" style="left:427px"><div class="img" role="img" aria-label="Flames rising from a grill with smoke" style="background:linear-gradient(160deg,#1c3a52,#d06a20 55%,#2a2a2a)"></div><span class="date">July 25,2019</span><h3>Lorem Ipsum is a dummy</h3><p>Lorem Ipsum is simply dummy text of the a printing and typesetting ever since indus-try Lorem Ipsum is simply dummy text of</p></article>
<article class="card" style="left:759px"><div class="img" role="img" aria-label="Meat being turned with tongs over open flames" style="background:linear-gradient(160deg,#2a1e16,#e0822a 55%,#3a2a20)"></div><span class="date">July 22,2019</span><h3>Lorem Ipsum is a dummy</h3><p>Lorem Ipsum is simply dummy text of the a printing and typesetting ever since indus-try Lorem Ipsum is simply dummy text of</p></article>
<div class="dots"><span></span><span class="on"></span><span></span></div>

<section class="map" role="img" aria-label="Road map showing the brand location"></section>

<footer class="footer">
  <h4 style="left:475px;top:60px">QUICK LINKS</h4>
  <ul class="links" style="left:476px;top:108px"><li>Home</li><li>About us</li><li>Products</li><li>Accessories</li><li>Contact</li></ul>
  <h4 style="left:667px;top:60px">OUR PRODUCTS</h4>
  <ul class="links" style="left:671px;top:98px"><li>Product Name</li><li>Product Name</li><li>Product Name</li><li>Product Name</li><li>Product Name</li></ul>
  <div class="footer-brand">BRASERO</div>
  <div class="social" style="left:880px" aria-label="Social link"></div>
  <div class="social" style="left:945px" aria-label="Social link"></div>
  <div class="social" style="left:1009px" aria-label="Social link"></div>
  <div class="social" style="left:1077px" aria-label="Social link"></div>
  <div class="divider" style="left:128px"></div>
  <div class="divider" style="left:1086px"></div>
  <div class="copyright">© Copyright 2023 by brasero</div>
</footer>

<form class="enquiry">
  <div class="enquiry-head">Send Enquiry</div>
  <div class="enquiry-body">
    <div class="field" style="top:40px">Your Name</div>
    <div class="field" style="top:91px">Email Address</div>
    <div class="field" style="top:148px">Mobile No</div>
    <div class="field" style="top:205px;padding-bottom:52px">Message</div>
    <div class="send">SEND</div>
  </div>
</form>

</body>
</html>
```